New B2C website design to help dads be better dads

DadHarbor is a website to help dads be the “best dad you can be.”

We require our website to be designed into a PSD format, no coding necessary.

The general concept is a two-page design. The first page is the login page, the second page is the home page. Once at the home page, rather than navigating to and from different pages, the user will push and pull through different visual and functional layers of the hierarchy. In theory, this should add to the user experience by having a visual anchor of where they are (through layered pagination) as well as improving loading times since the new information should only be a delta in data load versus a brand new page load.

The general look-and-feel we are going for is clean, simple, minimal. This means that the winning design will show us a good eye for web-optimized typography, good use of white (negative) space, and good use of a visually pleasing grid.

We require a total of 6 page "views" plus the landing page. We note that many of the views are similar to one another.
Landing page
Milestone view
Task view
Content view, articles
Content view, products
Search view
What's new view

Please review all of the additional information provided as well as the attachments for examples.

We provide the following websites as good references for:

Typography:
http://example-kelvorn.com/journal/

Use of white space:
http://www.trenvaskit.com/
http://moldrefin.com/

Example for “scrolling” page concept as well as good balance of color, typography, and white space:
http://www.qorbitalmeet.eu/

Please contact us with questions so that we can guide your design effort.
Updates

Hello designers,

The following information is added to help guide the design process:

1.  For the text dialogue below the landing page, please assume the following word count:
"why are we making dad harbor?": 250 words
"who are we?" 200 words
"what's the deal with the penguin logo?" 300 words

For the social media links, please see http://www.gravelplumbs.com/
Notice the floating "social" bar that is always to the right.  This is the concept we are going for, please try to implement this as you see fit. 

Target Market(s)

Fathers of young children ages 0-6 years old.

Industry/Entity Type

Product

Font styles to use
Sans Serif

Requirements
Must have
• Clean lines, minimal design concept

Incorporation of our logo (see attached document)

Header content is static for all views after landing page, see example

This page WILL be responsive, please keep that in mind when designing
The timeline bar should be to the left, with the timeline bar’s “milestones” also being responsive.

Designer is free to suggest font types, but any fonts used must be royalty-free and web-optimized. We request a minimum number of font types as well as fonts that load relatively fast. We reinforce that visually appealing typography is a significant factor in the winning design choice.

While we are not expecting the winning design to include code, please keep in mind that the final implementation needs to be optimized for desktop, tablet, and mobile platforms.

If you are using stock photography that is not generated by you, please provide where/how we can obtain imagery, as well as price.

All custom graphics must be available in original formats; Photoshop/GIMP layered files for layout design, and vector formats for logos, icons and other graphical elements.

Please incorporate “Blue” into design elements as you see fit, as the RGB 67 74 169 Blue is the primary color used in our brand. The complement to this blue is 255 202 0, a brownish orange. Feel free to use this color as well, although please keep it to a lesser amount.

Background color is your choice, do not feel the need to use the grey.
Should not have
• Excessive graphical content such that it affects loading times

Excessive use of too many font types such that it affects loading times

```html
<!DOCTYPE html>
<html lang="en">
<head>
<meta charset="utf-8">
<title>DadHarbor — Be the best dad you can be</title>
<link rel="stylesheet" href="https://fonts.googleapis.com/css2?family=Bebas+Neue&family=Raleway:wght@300;400;700;800&family=Questrial&display=swap">
<style>
  :root {
    --brand-blue: #434aa9;
    --hero-navy: #1c2670;
    --hero-deep: #0c1248;
    --hero-mid: #2f3d96;
    --hero-light: #5866b8;
    --brand-yellow: #ffca00;
    --paper: #ffffff;
    --sand: #f2eee0;
    --mist: #e9e9ea;
    --ink: #111111;
    --muted: #666666;
  }
  * { box-sizing: border-box; margin: 0; padding: 0; }
  html, body { width: 1200px; height: 2969px; overflow: hidden; }
  body { background: var(--paper); color: var(--ink); font-family: "Questrial", Arial, sans-serif; position: relative; }

  section, header, footer { position: relative; width: 1200px; overflow: hidden; }

  /* Hero */
  .hero { height: 705px; background: var(--hero-navy); }
  .hero-photo {
    position: absolute; inset: 0;
    background:
      radial-gradient(ellipse 380px 300px at 420px 380px, rgba(120,135,210,.55) 0%, rgba(120,135,210,0) 100%),
      radial-gradient(ellipse 320px 360px at 760px 300px, rgba(95,110,195,.55) 0%, rgba(95,110,195,0) 100%),
      radial-gradient(ellipse 260px 220px at 1020px 560px, rgba(80,95,180,.45) 0%, rgba(80,95,180,0) 100%),
      radial-gradient(ellipse 300px 200px at 200px 620px, rgba(70,85,170,.4) 0%, rgba(70,85,170,0) 100%),
      linear-gradient(160deg, var(--hero-deep) 0%, var(--hero-mid) 45%, var(--hero-navy) 75%, var(--hero-deep) 100%);
  }
  .hero-shade { position: absolute; inset: 0; background: linear-gradient(180deg, rgba(12,18,72,.55) 0%, rgba(12,18,72,0) 30%, rgba(12,18,72,0) 70%, rgba(12,18,72,.45) 100%); }
  .brand { position: absolute; left: 28px; top: 60px; display: flex; align-items: center; gap: 10px; color: #fff; font-family: "Raleway", sans-serif; font-weight: 800; font-size: 24px; }
  .brand-dot { width: 24px; height: 24px; border-radius: 50%; background: #fff; }
  .login { position: absolute; top: 35px; left: 490px; display: flex; gap: 12px; }
  .field { width: 208px; height: 47px; border: 2px solid rgba(255,255,255,.8); border-radius: 6px; background: rgba(20,28,90,.55); display: flex; align-items: center; gap: 10px; padding-left: 8px; color: #fff; font-size: 16px; font-family: "Raleway", sans-serif; font-weight: 700; }
  .field-icon { width: 26px; height: 26px; background: var(--brand-yellow); border-radius: 4px; display: flex; align-items: center; justify-content: center; }
  .btn-signin { width: 230px; height: 47px; border-radius: 6px; background: #6a74d6; color: #fff; font-family: "Raleway", sans-serif; font-weight: 800; font-size: 14px; letter-spacing: .5px; display: flex; align-items: center; justify-content: center; }
  .forgot { position: absolute; top: 92px; left: 715px; color: #fff; font-size: 12px; font-family: "Raleway", sans-serif; font-weight: 700; display: flex; align-items: center; gap: 6px; }
  .forgot::before { content: ""; width: 0; height: 0; border-left: 6px solid var(--brand-yellow); border-top: 4px solid transparent; border-bottom: 4px solid transparent; }
  .hero-title { position: absolute; left: 30px; top: 196px; color: var(--brand-yellow); font-family: "Bebas Neue", sans-serif; font-weight: 400; font-size: 70px; line-height: 1; letter-spacing: 1px; }
  .hero-sub { position: absolute; left: 32px; top: 260px; color: #fff; font-family: "Questrial", sans-serif; font-size: 31px; }
  .scroll-cue { position: absolute; left: 556px; top: 636px; }

  /* About heading */
  .about-head { height: 153px; display: flex; align-items: center; justify-content: center; }
  .about-head h2 { font-family: "Raleway", sans-serif; font-weight: 800; color: var(--brand-blue); font-size: 38px; letter-spacing: 1px; }

  .section-title { font-family: "Raleway", sans-serif; font-weight: 300; font-size: 42px; line-height: 1.2; }
  .copy { font-size: 14.5px; line-height: 23px; }

  /* Why */
  .why { height: 651px; background: var(--sand); }
  .why-photo { position: absolute; left: 0; top: 0; width: 500px; height: 651px; background: linear-gradient(100deg, #d4d1ca 0%, #e6e2d8 55%, var(--sand) 100%); }
  .why-accent { position: absolute; left: 0; top: 0; }
  .why .section-title { position: absolute; left: 153px; top: 85px; width: 300px; }
  .why .copy { position: absolute; left: 502px; top: 62px; width: 666px; }

  /* Who */
  .who { height: 544px; background: var(--mist); }
  .who-photo { position: absolute; inset: 0; background: linear-gradient(90deg, #c4c4c7 0%, #dedee0 40%, #f2f2f3 100%); }
  .who .section-title { position: absolute; top: 50px; width: 100%; text-align: center; font-size: 44px; }
  .who .copy { position: absolute; left: 225px; top: 136px; width: 750px; text-align: center; }

  /* Penguin */
  .penguin { height: 582px; background: var(--brand-blue); color: #fff; }
  .penguin .section-title { position: absolute; left: 148px; top: 62px; width: 270px; }
  .penguin-art { position: absolute; left: 150px; top: 270px; width: 240px; height: 312px; border-radius: 120px 120px 0 0; background: linear-gradient(180deg, rgba(255,255,255,.9), rgba(255,255,255,.7)); }
  .penguin .copy { position: absolute; left: 502px; top: 66px; width: 662px; }

  /* Footer */
  .contact { height: 334px; text-align: center; }
  .contact-label { position: absolute; top: 38px; width: 100%; font-family: "Raleway", sans-serif; font-weight: 700; font-size: 13px; letter-spacing: 3px; color: var(--muted); }
  .contact-title { position: absolute; top: 76px; width: 100%; font-family: "Raleway", sans-serif; font-weight: 300; font-size: 40px; }
  .contact-mail { position: absolute; top: 148px; width: 100%; font-family: "Raleway", sans-serif; font-weight: 700; font-size: 19px; color: var(--brand-blue); }
  .social { position: absolute; top: 196px; left: 0; width: 100%; display: flex; justify-content: center; gap: 36px; }
  .social-link { width: 56px; height: 56px; border-radius: 50%; border: 2px solid #d5d7ea; display: flex; align-items: center; justify-content: center; font-family: "Raleway", sans-serif; font-weight: 700; font-size: 9px; color: var(--brand-blue); text-decoration: none; }
  .legal { position: absolute; top: 284px; width: 100%; font-size: 12px; color: #333; }
</style>
</head>
<body>

<header class="hero">
  <div class="hero-photo" role="img" aria-label="Blue-toned photograph of a father and his young child"></div>
  <div class="hero-shade"></div>
  <div class="brand"><span class="brand-dot"></span>DadHarbor</div>
  <form class="login">
    <div class="field"><span class="field-icon"><svg width="16" height="16" viewBox="0 0 16 16"><circle cx="8" cy="5" r="3.2" fill="#1c2670"/><path d="M2 15c0-3.5 2.7-5.5 6-5.5s6 2 6 5.5z" fill="#1c2670"/></svg></span>Username</div>
    <div class="field"><span class="field-icon"><svg width="16" height="16" viewBox="0 0 16 16"><circle cx="5" cy="8" r="3.2" fill="none" stroke="#1c2670" stroke-width="2"/><path d="M8 8h7M12 8v3M14.5 8v2.5" stroke="#1c2670" stroke-width="2" fill="none"/></svg></span>Password</div>
    <div class="btn-signin">SIGN IN / REQUEST ACCESS</div>
  </form>
  <div class="forgot">Forgot login?</div>
  <h1 class="hero-title">BE THE BEST DAD YOU CAN BE</h1>
  <p class="hero-sub">The portal created exclusively for dads, by dads</p>
  <svg class="scroll-cue" width="88" height="44" viewBox="0 0 88 44" aria-hidden="true">
    <path d="M4 4 L44 36 L84 4" fill="none" stroke="#ffca00" stroke-width="5"/>
    <path d="M18 4 L44 24 L70 4" fill="none" stroke="#ffca00" stroke-width="4"/>
  </svg>
</header>

<section class="about-head"><h2>ABOUT DAD HARBOR</h2></section>

<section class="why">
  <div class="why-photo" role="img" aria-label="Soft photograph of a smiling father holding his child"></div>
  <svg class="why-accent" width="500" height="460" aria-hidden="true">
    <polygon points="0,0 495,0 0,428" fill="#ffca00"/>
    <circle cx="200" cy="150" r="150" fill="#ffca00" opacity=".85"/>
  </svg>
  <h3 class="section-title">Why are we making dad harbor?</h3>
  <p class="copy">Lorem ipsum dolor sit amet, consectetur adipisicing elit, sed do eiusmod tempor incididunt ut labore et dolore magna aliqua. Ut enim ad minim veniam, quis nostrud exercitation ullamco laboris nisi ut aliquip ex ea commodo consequat. Duis aute irure dolor in reprehenderit in voptate velit esse cillum dolore eu fugiat nulla paritur. Excepteur sint occaecat cupidatat non proident, sunt in culpa qui officia deserunt mollit anim id est laborum. Lorem ipsum dolor sit amet, consectetur adipisicing elit, sed do eiusd tmor incididunt ut labore et dolore magna aliqua. Ut enim ad minim veniam, quis nostrud exercitation ullamco laboris nisi ut aliquip ex ea commodo consequat. Duis aute irure dolor in reheder it in volute velit esse cillum dolore eu fugiat nulla paiatur. Excpteur sint occaecat cidatat non proident, sunt in culpa qui officia deserunt molit anim id est laborum. Lorem ipsum dolor sit amet, contur adiscing elit, sed do eiumod tempor incididunt ut labore et dolore magna aliqua. Ut enim ad mnim veniam, quis nostud exercitation ullmco laboris nisi ut aliquip ex ea commodo conequat. Duis aute irure door in reprehenderit in voluptate velit esse cillum dolore eu fugiat nulla pariatur. Excepteur sint occaecat cupidatat non proident, sunt in culpa qui officia deserunt mollit anim id est laborum. Lorem ipsum dolor sit amet, consectetur adipisicing elit, sed do eiusmod tempor incididunt ut labore et dolore magna aliqua. Ut enim ad minim veniam, quis nostrud exercitation ullamco laboris nisi ut aliquip ex ea commodo consequat. Duis aute irure dolor in reprehenderit.</p>
</section>

<section class="who">
  <div class="who-photo" role="img" aria-label="Faded photograph of a small child seen from behind on a father's shoulders"></div>
  <h3 class="section-title">Who are we?</h3>
  <p class="copy">Lorem ipsum dolor sit amet, consectetur adipisicing elit, sed do eiusmod tempor incididunt ut labore et dolore magna aliqua. Ut enim ad minim veniam, quis nostrud exercitation ullamco laboris nisi ut aliqip ex ea commodo cnsequat. Duis aute irure dolor in reprehenderit in voptate velit esse cillum dolore eu fugiat nulla paritur. Excepteur sint occaecat cupidatat non proident, sunt in culpa qui officia deserunt mollit anim id est laborum. Lorem ipsum dolor sit amet, consectetur adipisicing elit, sed do eiusd tmor incididunt ut labore et dolore magna aliqua. Ut enim ad minim veniam, quis nostrud exercitation ullamco laboris nisi ut aliquip ex ea commodo consequat. Duis aute irure dolor in reheder it in volute velit esse cillum dolore eu fugiat nulla paiatur. Excpteur sint occaecat cidatat non proident, sunt in culpa qui officia deserunt molit anim id est laborum. Lorem ipsum dolor sit amet, contur adiscing elit, sed do eiumod tempor incididunt ut labore et dolore magna aliqua. Ut enim ad mnim veniam, quis nostrud exercitation ullamco laboris nisi ut aliquip ex ea commodo consequat. Duis aute irure dolor in reprehenderit in voluptate velit esse cillum dolore eu fugiat nulla pariatur. Excepteur sint occaecat cupidatat non proident, sunt in culpa.</p>
</section>

<section class="penguin">
  <h3 class="section-title">What’s the deal with the penguin logo?</h3>
  <div class="penguin-art" role="img" aria-label="Large white penguin illustration, the brand mascot"></div>
  <p class="copy">Lorem ipsum dolor sit amet, consectetur adipisicing elit, sed do eiusmod tempor incididunt ut labore et dolore magna aliqua. Ut enim ad minim veniam, quis nostrud exercitation ullamco laboris nisi ut aliqip ex ea commodo cnsequat. Duis aute irure dolor in reprehenderit in voptate velit esse cillum dolore eu fugiat nulla paritur. Excepteur sint occaecat cupidatat non proident, sunt in culpa qui officia deserunt mollit anim id est laborum. Lorem ipsum dolor sit amet, consectetur adipisicing elit, sed do eiusd tmor incididunt ut labore et dolore magna aliqua. Ut enim ad minim veniam, quis nostrud exercitation ullamco laboris nisi ut aliquip ex ea commodo consequat. Duis aute irure dolor in reheder it in volute velit esse cillum dolore eu fugiat nulla paiatur. Excpteur sint occaecat cidatat non proident, sunt in culpa qui officia deserunt molit anim id est laborum. Lorem ipsum dolor sit amet, contur adiscing elit, sed do eiumod tempor incididunt ut labore et dolore magna aliqua. Ut enim ad mnim veniam, quis nostud exercitation ullmco laboris nisi ut aliquip ex ea commodo conequat. Duis aute irure door in reprehenderit in voluptate velit esse cillum dolore eu fugiat nulla pariatur. Excepteur sint occaecat cupidatat non proident, sunt in culpa.</p>
</section>

<footer class="contact">
  <p class="contact-label">CONTACT</p>
  <h3 class="contact-title">GET IN TOUCH</h3>
  <p class="contact-mail">info@dadharbor.com</p>
  <nav class="social" aria-label="Social links">
    <a class="social-link" href="#">Chirpline</a>
    <a class="social-link" href="#">Facetab</a>
    <a class="social-link" href="#">Linkward</a>
  </nav>
  <p class="legal">Privacy Policy &nbsp;|&nbsp; © 2013 DadHarbor &nbsp;|&nbsp; Terms Policy &nbsp;|&nbsp; Disclaimer</p>
</footer>

</body>
</html>
```